American cannabis tech company business card design

Pavrel.com is seeking a modern, professional, and brand-aligned business card that represents our company and its core values: Mission, Story, Values, and Impact. As an innovative cannabis company, we want a business card that is not only visually appealing but also serves as a representation of who we are and what we stand for.

Project Scope: Design a double-sided business card that integrates our brand identity and core values. Incorporate our key brand elements, ensuring a sleek and contemporary aesthetic. Visually reflect our core values (Mission, Story, Values, Impact) in a way that is engaging yet professional.

Target Market(s)

Vendors, third parties,

Contact Information for Business Card

Contact details (name, title, email, phone, website, etc.)

Font styles to use
Other font styles liked:
• Caslon, Centra

Colors

Designer to choose colors to be used in the design.

Requirements
Must have
• Pavrel.com logo and branding A creative yet clean way to integrate our core values (Mission, Story, Values, Impact) Modern typography and a well-structured layout
Nice to have
• forest green, grey, white, black
Should not have
• references to marijuana, leafs, plants, or related product

```html
<!DOCTYPE html>
<html lang="en">
<head>
<meta charset="UTF-8">
<title>Pavrel.com Business Card</title>
<link href="https://fonts.googleapis.com/css2?family=Poppins:wght@400;600;700;800&display=swap" rel="stylesheet">
<style>
  :root {
    --backdrop: #1f1f20;
    --forest: #1b3a1c;
    --forest-deep: #163218;
    --leaf: #2e6b34;
    --white: #ffffff;
  }
  * { margin: 0; padding: 0; box-sizing: border-box; }
  html, body {
    width: 1200px;
    height: 1015px;
    overflow: hidden;
    background: var(--backdrop);
    font-family: "Poppins", sans-serif;
  }
  .stage {
    position: relative;
    width: 1200px;
    height: 1015px;
  }
  .card {
    position: absolute;
    width: 620px;
    height: 354px;
    border-radius: 4px;
    overflow: hidden;
    box-shadow: 0 12px 30px rgba(0,0,0,0.45);
  }
  /* Back side */
  .card--back {
    left: 70px;
    top: 110px;
    background: var(--forest);
    display: flex;
    align-items: center;
    justify-content: center;
  }
  .card--back .brand-name {
    font-weight: 800;
    font-size: 92px;
    letter-spacing: 2px;
    color: var(--leaf);
  }
  /* Front side */
  .card--front {
    left: 510px;
    top: 540px;
    background: var(--forest);
  }
  .card--front .emblem {
    position: absolute;
    inset: 0;
  }
  .card--front .brand-name {
    position: absolute;
    left: 330px;
    top: 120px;
    width: 280px;
    text-align: center;
    font-weight: 800;
    font-size: 54px;
    letter-spacing: 1px;
    color: var(--forest);
  }
  .holder {
    position: absolute;
    left: 40px;
    top: 96px;
    color: var(--white);
  }
  .holder__name {
    font-weight: 700;
    font-size: 21px;
    letter-spacing: 0.5px;
    line-height: 1.15;
  }
  .holder__title {
    font-weight: 400;
    font-size: 14px;
  }
  .contact {
    position: absolute;
    left: 40px;
    bottom: 34px;
    list-style: none;
    color: var(--white);
    font-size: 15px;
    line-height: 1.45;
  }
  .contact li {
    display: flex;
    align-items: center;
    gap: 8px;
  }
  .contact svg {
    width: 15px;
    height: 15px;
    flex: none;
  }
</style>
</head>
<body>
<main class="stage">

  <section class="card card--back" aria-label="Card back">
    <span class="brand-name">PAVREL</span>
  </section>

  <section class="card card--front" aria-label="Card front">
    <svg class="emblem" viewBox="0 0 620 354" aria-hidden="true">
      <circle cx="470" cy="150" r="214" fill="none" stroke="var(--white)" stroke-width="4" transform="translate(-10 8)"/>
      <circle cx="480" cy="140" r="200" fill="var(--white)"/>
    </svg>
    <span class="brand-name">PAVREL</span>

    <div class="holder">
      <p class="holder__name">DANIEL HARPER</p>
      <p class="holder__title">Managing Director</p>
    </div>

    <ul class="contact">
      <li>
        <svg viewBox="0 0 24 24" fill="var(--white)"><path d="M6.6 10.8a15.1 15.1 0 0 0 6.6 6.6l2.2-2.2a1 1 0 0 1 1-.25 11.4 11.4 0 0 0 3.6.57 1 1 0 0 1 1 1V20a1 1 0 0 1-1 1A17 17 0 0 1 3 4a1 1 0 0 1 1-1h3.5a1 1 0 0 1 1 1c0 1.25.2 2.45.57 3.6a1 1 0 0 1-.25 1z"/></svg>
        044-555 010 234
      </li>
      <li>
        <svg viewBox="0 0 24 24" fill="none" stroke="var(--white)" stroke-width="2"><rect x="2" y="5" width="20" height="14" rx="1"/><path d="M2 6l10 7 10-7"/></svg>
        info@pavrel.com
      </li>
      <li>
        <svg viewBox="0 0 24 24" fill="none" stroke="var(--white)" stroke-width="2"><circle cx="12" cy="12" r="10"/><path d="M2 12h20M12 2c3 3 3 17 0 20M12 2c-3 3-3 17 0 20"/></svg>
        www.pavrel.com
      </li>
    </ul>
  </section>

</main>
</body>
</html>
```